Norrell Advisory WA Business Card

Create an interesting, eye catching and colourful two sided business card. We are a business consulting operation assisting SME's improve all areas of their business. We provide consulting services to assist SME's to create a culture of continuous improvement, making a positive difference in the business. Our tag line is Small changes, big rewards. We want to create a well recognised, innovative brand that can be continued throughout our website, social media and email correspondence.

Target Market(s)

Small to Medium Enterprise Business Owners

Industry/Entity Type

Business Consultant

Contact Information for Business Card

Name of Business: Norrell Advisory - Steady steps strong results
Derek Holloway Ph 0407385510 Megan Holloway Ph 0407913847
Email norrelladvisorywa@mailbox-example.com
Web address TBA
FaceBook page TBA

BACKSIDE OF CARD

Providing assistance with:

• Organisation & Efficiency
• Revenue generation & Marketing
• Financial Management
• Production quality & delivery
• Systems & Process documentation
• Exit Strategy

Font styles to use
Other font styles liked:
• Calibri

Colors

Designer to choose colors to be used in the design.

Requirements
Must have
• Calibri font

```html
<!DOCTYPE html>
<html lang="en">
<head>
<meta charset="utf-8">
<title>Norrell Advisory WA – Business Card</title>
<link rel="stylesheet" href="https://fonts.googleapis.com/css2?family=Carlito:wght@400;700&display=swap">
<style>
  :root {
    --page: #e9e9e9;
    --card-white: #ffffff;
    --band-dark: #2e2c2c;
    --back-dark: #2b2a27;
    --back-dark-2: #302c2a;
    --ink: #2b2b2b;
    --ink-soft: #555555;
    --brand-blue: #1b76b8;
    --icon-blue: #2f86c6;
    --white: #ffffff;
  }
  * { box-sizing: border-box; margin: 0; padding: 0; }
  html, body {
    width: 1125px; height: 1200px; overflow: hidden;
    background: var(--page);
    font-family: "Carlito", "Calibri", sans-serif;
  }
  .canvas { position: relative; width: 1125px; height: 1200px; }

  .card { position: absolute; left: 171px; width: 826px; height: 471px; overflow: hidden; }

  /* Front */
  .card--front { top: 106px; background: var(--card-white); }
  .front__brand { position: absolute; left: 58px; top: 68px; }
  .brand-name {
    font-weight: 700; font-size: 35px; line-height: 1; color: var(--ink);
    text-transform: uppercase; letter-spacing: 0.2px;
  }
  .brand-tagline {
    margin-top: 5px; font-size: 19px; line-height: 1; color: var(--ink-soft);
    text-transform: uppercase; letter-spacing: 1.6px;
  }
  .front__band {
    position: absolute; left: 0; top: 207px; width: 100%; height: 212px;
    background: var(--band-dark);
  }
  .contact { position: absolute; left: 58px; top: 32px; color: var(--white); }
  .contact__name { font-weight: 700; font-size: 29px; line-height: 1; color: var(--brand-blue); }
  .contact__phone { margin-top: 4px; font-weight: 700; font-size: 17px; line-height: 1.1; }
  .contact__list { list-style: none; margin-top: 20px; }
  .contact__item {
    display: flex; align-items: center; gap: 10px;
    font-size: 18px; line-height: 25px;
  }
  .contact__icon { width: 18px; height: 18px; flex: none; }
  .front__mark {
    position: absolute; left: 520px; top: 90px;
    display: flex; align-items: center; gap: 12px;
  }
  .mark-square { width: 22px; height: 22px; background: var(--icon-blue); }
  .mark-name { font-weight: 700; font-size: 26px; line-height: 1; color: var(--white); }

  /* Back */
  .card--back { top: 639px; }
  .back__pattern {
    position: absolute; inset: 0;
    background: radial-gradient(ellipse at 40% 50%, var(--back-dark-2), var(--back-dark) 75%);
  }
  .back__brand {
    position: absolute; left: 227px; top: 140px; transform: translateX(-50%);
    text-align: center; color: var(--white); white-space: nowrap;
  }
  .back__square { width: 60px; height: 60px; margin: 0 auto 78px; background: var(--icon-blue); }
  .back__brand .brand-name { color: var(--white); font-size: 29px; }
  .back__brand .brand-tagline { color: var(--white); font-size: 17px; margin-top: 4px; letter-spacing: 1.4px; }
  .services { position: absolute; left: 426px; top: 128px; color: var(--white); }
  .services__title { font-weight: 700; font-size: 28px; line-height: 1; color: var(--brand-blue); }
  .services__list { list-style: none; margin-top: 18px; }
  .services__item {
    display: flex; align-items: center; gap: 7px;
    font-size: 19px; line-height: 26.3px;
  }
  .services__bullet { width: 12px; height: 12px; flex: none; background: var(--icon-blue); }
</style>
</head>
<body>
<div class="canvas">

  <section class="card card--front" aria-label="Business card front">
    <div class="front__brand">
      <h1 class="brand-name">Norrell Advisory</h1>
      <p class="brand-tagline">Steady steps strong results</p>
    </div>
    <div class="front__band">
      <div class="contact">
        <p class="contact__name">Megan Holloway</p>
        <p class="contact__phone">0407913847</p>
        <ul class="contact__list">
          <li class="contact__item">
            <svg class="contact__icon" viewBox="0 0 18 18" aria-hidden="true">
              <rect x="1" y="4" width="16" height="11" fill="var(--icon-blue)"/>
              <path d="M1 4 L9 10 L17 4" fill="none" stroke="var(--band-dark)" stroke-width="1.4"/>
            </svg>
            norrelladvisorywa@mailbox-example.com
          </li>
          <li class="contact__item">
            <svg class="contact__icon" viewBox="0 0 18 18" aria-hidden="true">
              <circle cx="9" cy="9" r="8" fill="var(--icon-blue)"/>
              <ellipse cx="9" cy="9" rx="3.5" ry="8" fill="none" stroke="var(--band-dark)" stroke-width="1.2"/>
              <line x1="1" y1="9" x2="17" y2="9" stroke="var(--band-dark)" stroke-width="1.2"/>
            </svg>
            www.norrelladvisorywa.com
          </li>
          <li class="contact__item">
            <svg class="contact__icon" viewBox="0 0 18 18" aria-hidden="true">
              <rect x="2" y="2" width="14" height="14" fill="var(--icon-blue)"/>
            </svg>
            norrelladvisorywa
          </li>
        </ul>
      </div>
      <div class="front__mark">
        <span class="mark-square" aria-hidden="true"></span>
        <span class="mark-name">Norrell Advisory</span>
      </div>
    </div>
  </section>

  <section class="card card--back" aria-label="Business card back">
    <div class="back__pattern" role="img" aria-label="Dark background pattern of interlocking shapes in muted red, green and blue"></div>
    <div class="back__brand">
      <div class="back__square" aria-hidden="true"></div>
      <h2 class="brand-name">Norrell Advisory</h2>
      <p class="brand-tagline">Steady steps strong results</p>
    </div>
    <div class="services">
      <h3 class="services__title">Providing assistance with</h3>
      <ul class="services__list">
        <li class="services__item"><span class="services__bullet"></span>Organisation &amp; Efficiency</li>
        <li class="services__item"><span class="services__bullet"></span>Revenue generation &amp; Marketing</li>
        <li class="services__item"><span class="services__bullet"></span>Financial Management</li>
        <li class="services__item"><span class="services__bullet"></span>Production quality &amp; delivery</li>
        <li class="services__item"><span class="services__bullet"></span>Systems &amp; Process documentation</li>
        <li class="services__item"><span class="services__bullet"></span>Exit Strategy</li>
      </ul>
    </div>
  </section>

</div>
</body>
</html>
```